KORVA needs a beautiful/corp web page

We are a pump an compressor repair facility in Alberta Canada. We love clean looks. white yellows greens blues. main page should involve conola fields, sun shine

Reason: i will be guaranteeing the project keep up the good work

Requirements
Must have
• open conola fields

```html
<!DOCTYPE html>
<html lang="en">
<head>
<meta charset="utf-8">
<title>KORVA Rotating Solutions</title>
<link rel="stylesheet" href="https://fonts.googleapis.com/css2?family=Montserrat:wght@400;600;700;800&family=Arimo:wght@400;700&display=swap">
<style>
  :root {
    --field-green: #779304;
    --brand-orange: #f4a70b;
    --ink: #262222;
    --body-grey: #666666;
    --rule-grey: #cfcfcf;
    --footer-bg: #282424;
    --white: #ffffff;
    --sky-top: #5f9fe0;
    --sky-mid: #bcd8f2;
    --canola: #f2dd12;
    --canola-deep: #d9b80a;
  }
  * { box-sizing: border-box; margin: 0; padding: 0; }
  html, body { width: 1200px; height: 836px; overflow: hidden; }
  body {
    background: var(--field-green);
    font-family: "Arimo", Arial, sans-serif;
    color: var(--ink);
  }
  .page {
    position: absolute; left: 185px; top: 0;
    width: 832px; height: 836px;
    background: var(--white);
    box-shadow: 0 0 12px rgba(0,0,0,0.35);
  }

  /* Hero */
  .hero { position: relative; height: 453px; overflow: hidden; }
  .hero-photo {
    position: absolute; inset: 0;
    background: linear-gradient(180deg, var(--sky-top) 0%, var(--sky-mid) 22%, #e6eef4 40%, var(--canola) 58%, var(--canola) 80%, var(--canola-deep) 100%);
  }
  .brand {
    position: absolute; left: 36px; top: 86px;
    display: flex; align-items: center; gap: 8px;
  }
  .brand-dot { width: 18px; height: 18px; border-radius: 50%; background: var(--brand-orange); }
  .brand-name {
    font-family: "Montserrat", sans-serif; font-weight: 800;
    font-size: 36px; line-height: 36px; letter-spacing: 1px; color: var(--ink);
  }
  .main-nav {
    position: absolute; left: 272px; top: 64px;
    width: 560px; height: 33px;
    background: var(--brand-orange);
    display: flex; align-items: center; justify-content: space-around;
    padding: 0 8px 0 14px;
  }
  .main-nav a {
    font-family: "Arimo", sans-serif; font-size: 12px;
    color: var(--white); text-decoration: none; text-transform: uppercase;
  }
  .main-nav .sep { width: 1px; height: 10px; background: #b36d00; }
  .hero-copy {
    position: absolute; left: 0; right: 0; top: 196px; text-align: center;
  }
  .hero-title {
    font-family: "Montserrat", sans-serif; font-weight: 800;
    font-size: 33px; line-height: 41px; color: var(--white);
    text-transform: uppercase; letter-spacing: 0.3px;
    text-shadow: 0 0 3px rgba(0,0,0,0.55), 0 2px 4px rgba(0,0,0,0.35);
  }
  .hero-lede {
    margin: 14px auto 0; width: 440px;
    font-size: 12px; line-height: 16px; color: #111;
  }
  .hero-btn {
    display: inline-block; margin-top: 24px;
    width: 114px; height: 34px; line-height: 30px;
    border: 2px solid var(--white);
    font-size: 12px; color: #222; text-decoration: none;
  }

  /* Intro */
  .intro { position: relative; height: 267px; }
  .intro-photo {
    position: absolute; left: 17px; top: 21px; width: 159px; height: 212px;
    background: linear-gradient(180deg, #c9d4dc 0%, #d9e0e2 12%, #e9d623 20%, #6b7a25 30%, #e8d012 40%, #f2dd12 70%, #c8a80a 100%);
  }
  .welcome { position: absolute; left: 198px; top: 22px; width: 350px; }
  .section-title {
    font-family: "Montserrat", sans-serif; font-weight: 600;
    font-size: 24px; color: var(--ink);
  }
  .section-title .accent { color: var(--brand-orange); }
  .welcome p {
    margin-top: 12px; font-size: 11px; line-height: 18px; color: var(--body-grey);
  }
  .welcome p + p { margin-top: 17px; }
  .more-link {
    display: flex; align-items: center; gap: 8px; margin-top: 20px;
    font-family: "Montserrat", sans-serif; font-weight: 700; font-size: 11px;
    color: var(--ink); text-decoration: none;
  }
  .services { position: absolute; left: 577px; top: 22px; width: 230px; }
  .service-list { list-style: none; margin-top: 10px; }
  .service-list li {
    display: flex; align-items: center; gap: 10px;
    height: 31px; padding-left: 10px;
    font-size: 11px; color: var(--body-grey);
  }
  .service-list li span {
    flex: 1; height: 31px; line-height: 31px;
    border-bottom: 1px dashed var(--rule-grey);
  }

  /* Footer */
  .site-footer {
    position: absolute; left: 0; top: 720px; width: 832px; height: 116px;
    background: var(--footer-bg); color: var(--white);
  }
  .footer-title {
    position: absolute; left: 30px; top: 18px;
    font-family: "Montserrat", sans-serif; font-weight: 700; font-size: 15px;
  }
  .footer-title .accent { color: var(--brand-orange); }
  .footer-col {
    position: absolute; top: 46px;
    font-size: 9.5px; line-height: 12px;
  }
  .footer-col.address { left: 30px; font-weight: 700; }
  .footer-col.phones { left: 181px; }
  .footer-col .mail { color: var(--brand-orange); }
  .social { position: absolute; left: 745px; top: 37px; display: flex; gap: 7px; }
  .social a {
    width: 27px; height: 26px; display: block;
    background: var(--brand-orange); color: var(--white);
    font-family: "Arimo", sans-serif; font-weight: 700; font-size: 8px;
    line-height: 26px; text-align: center; text-decoration: none;
  }
  .copyright {
    position: absolute; right: 21px; top: 74px; font-size: 9.5px;
  }
</style>
</head>
<body>
<div class="page">
  <header class="hero">
    <div class="hero-photo" role="img" aria-label="Open canola field in full yellow bloom under a bright blue sky with white clouds"></div>
    <div class="brand"><span class="brand-dot"></span><span class="brand-name">KORVA</span></div>
    <nav class="main-nav">
      <a href="#">Home</a><span class="sep"></span>
      <a href="#">About Us</a><span class="sep"></span>
      <a href="#">Our Services</a><span class="sep"></span>
      <a href="#">Our&nbsp; Products</a><span class="sep"></span>
      <a href="#">Contact Us</a>
    </nav>
    <div class="hero-copy">
      <h1 class="hero-title">Offers a variety of options<br>for your rotating solutions</h1>
      <p class="hero-lede">We are a service provider and process equipment supplier of pump products and customized compressor systems.</p>
      <a class="hero-btn" href="#">READ MORE</a>
    </div>
  </header>

  <section class="intro">
    <div class="intro-photo" role="img" aria-label="Canola field in bloom stretching to the horizon"></div>
    <article class="welcome">
      <h2 class="section-title">Welcome to <span class="accent">Korva</span></h2>
      <p>Proin gravida nibh vel velit auctor aliquet. Aenean sollicitudin, lorem quis bibendum auctor, nisi elit consequat ipsum, nec sagittis sem nibh id elit. Duis sed odio sit amet nibh vulputate cursus a sit amet mauris. Morbi accumsan ipsum velit. Nam nec tellus a odio tincidunt auctor a</p>
      <p>Ornare odio. Sed non&nbsp; mauris vitae erat consequat auctor eu in elit.<br>per inceptos himenaeos. Mauris in erat justo. Nullam ac urna eu felis</p>
      <a class="more-link" href="#">READ MORE
        <svg width="8" height="10" viewBox="0 0 8 10"><path d="M1.5 1l4 4-4 4" fill="none" stroke="#f4a70b" stroke-width="2"/></svg>
      </a>
    </article>
    <aside class="services">
      <h2 class="section-title">Our <span class="accent">Service</span></h2>
      <ul class="service-list">
        <li><svg width="8" height="10" viewBox="0 0 8 10"><path d="M1.5 1l4 4-4 4" fill="none" stroke="#f4a70b" stroke-width="2"/></svg><span>Proin gravida nibh vel velit auctor</span></li>
        <li><svg width="8" height="10" viewBox="0 0 8 10"><path d="M1.5 1l4 4-4 4" fill="none" stroke="#f4a70b" stroke-width="2"/></svg><span>Aliquet. Aenean sollicitudin, lorem</span></li>
        <li><svg width="8" height="10" viewBox="0 0 8 10"><path d="M1.5 1l4 4-4 4" fill="none" stroke="#f4a70b" stroke-width="2"/></svg><span>Quis bibendum auctor, nisi elit</span></li>
        <li><svg width="8" height="10" viewBox="0 0 8 10"><path d="M1.5 1l4 4-4 4" fill="none" stroke="#f4a70b" stroke-width="2"/></svg><span>Consequat ipsum, nec sagittis sem</span></li>
        <li><svg width="8" height="10" viewBox="0 0 8 10"><path d="M1.5 1l4 4-4 4" fill="none" stroke="#f4a70b" stroke-width="2"/></svg><span>Nibh id elituis sed odio sit amet nibh</span></li>
      </ul>
    </aside>
  </section>

  <footer class="site-footer">
    <h3 class="footer-title">CONTACT <span class="accent">US</span></h3>
    <div class="footer-col address">Lorem Ipsum Stree,&nbsp; Block 234<br>Nam Tellus, 1234, TA,<br>Country , USA</div>
    <div class="footer-col phones">P: 1800-555014<br>F: 1023- 555231<br>E: <span class="mail">info@korvapumps.ca</span></div>
    <div class="social">
      <a href="#" aria-label="Vela profile">Vela</a>
      <a href="#" aria-label="Orbi profile">Orbi</a>
    </div>
    <p class="copyright">Copyright © 2013&nbsp; Korva Rotating Solution, All Rights Reserved</p>
  </footer>
</div>
</body>
</html>
```